Trucking Company Website Design

We are working with a Trucking company in California. They provide trucking services for dirt, gravel, landscape bark, and landscape materials.

As you might imagine, there are no websites we could find for inspiration for trucking companies.

Thank you for taking the time to consider designing a website for us. We are web developers based in Stockton, CA, USA. Most of our projects go through the same process. Understanding this process may help you win a project with us. We custom-code all of our websites in-house. We don’t have any requirements as to what tools you use for your design, but we ask that you follow these guidelines.

IMAGES:
If you use any images or icons in the design, we ask that you have a link to the asset so we can purchase the image/icon. Most of the designs we submit do not have the customer’s images on them unless they have some great images. Be creative; show us the feeling you are trying to portray with your image choices. Use any royalty-free site you choose. We subscribe to Quillo and mainly use their images, but we can purchase images outside of Quillo. PLEASE NOTE: we will not submit designs to clients with watermarks on the images.

FONTS:
We ask that you identify the fonts you’re using in the design. This can be done in a message if you want. We typically use Varnex Fonts and Quillo Fonts.

CONTENT:
We're always open to different content and ideas. We often submit designs with stock images so the client can see our vision. We typically take pictures after the website launch to use their images with our vision. Lorem Ipsum is fine for paragraphs, but we ask that you make the Headers with correct English. We want to be able to show the vision and identify the sections of the website.

INSPIRATION:
We typically add a couple of links in the brief of websites we like to help you get started in your design.

REVISIONS:
We do not often ask for revisions of the designs unless we see something in the design that may not appeal to the client. If there are slight changes that we want to make, we do that in the development process.

FEEDBACK:
We rarely give feedback on designs during the design process. We are working on many website projects and do not have the time to provide feedback. We usually respond if your request is well thought out and asks specific questions, but a note asking “feedback, please” usually goes unanswered.

```html
<!DOCTYPE html>
<html lang="en">
<head>
<meta charset="utf-8">
<title>Summit Aggregates – Trucking</title>
<link rel="stylesheet" href="https://fonts.googleapis.com/css2?family=Exo+2:wght@500;600;700&family=Raleway:wght@400;500;600&display=swap">
<style>
:root{
  --blue:#1a7bb5;
  --red:#e31b2d;
  --ink:#1d1d1d;
  --grey:#555;
  --black:#050505;
  --white:#fff;
}
*{box-sizing:border-box;margin:0;padding:0}
html,body{width:1200px;height:3130px;overflow:hidden}
body{position:relative;font-family:"Raleway",sans-serif;color:var(--ink);background:var(--white)}
.abs{position:absolute}
.heading{font-family:"Exo 2",sans-serif;font-weight:600;letter-spacing:.5px}
.brand{display:flex;align-items:center;gap:10px;font-family:"Raleway",sans-serif;font-weight:600;color:var(--blue);font-size:27px;letter-spacing:.5px;white-space:nowrap}
.brand-square{width:28px;height:28px;background:var(--red);flex:none}
.contact-item{display:flex;align-items:center;gap:18px;font-size:14px;line-height:18px}
.contact-item b{font-weight:600}
.round-icon{width:42px;height:42px;border-radius:50%;background:var(--red);display:flex;align-items:center;justify-content:center}
.btn{display:flex;align-items:center;justify-content:center;color:var(--white);font-size:14px;font-weight:600}
.btn-blue{background:var(--blue)}
.btn-red{background:var(--red)}
.nav{display:flex;align-items:center;font-size:14.5px;font-weight:500;color:var(--white);white-space:nowrap}
.nav span.sep{margin:0 20px}
.hero{left:0;top:102px;width:1200px;height:520px;background:linear-gradient(160deg,#6e7c4a 0%,#a3804f 30%,#8c8f8e 55%,#a98459 75%,#7a8c7a 100%)}
.section-title{width:1200px;text-align:center;font-size:40px;color:var(--ink)}
.card{width:232px;height:257px;background:var(--white);box-shadow:0 4px 22px rgba(0,0,0,.10);border-radius:8px;text-align:center;padding-top:26px}
.service-icon{width:64px;height:60px;margin:0 auto;border-radius:8px;background:linear-gradient(135deg,#d6e8f4,#a9cde6)}
.card h3{font-size:14.5px;font-weight:600;margin-top:18px;letter-spacing:.3px}
.card p{font-size:13px;color:var(--grey);line-height:26.5px;margin:10px 18px 0}
.about{left:0;top:1096px;width:1200px;height:430px;background:var(--blue)}
.about-text{left:114px;top:1150px;width:560px;color:var(--white)}
.about-text h2{font-size:42px;font-weight:600}
.about-text p{font-size:15px;line-height:30px;margin-top:14px}
.quote-wrap{filter:drop-shadow(0 4px 12px rgba(0,0,0,.14))}
.quote-card{width:456px;height:218px;background:var(--white)}
.quote-badge{width:80px;height:80px;border-radius:50%;background:var(--red);box-shadow:0 4px 0 #b3111f;display:flex;align-items:center;justify-content:center;color:var(--white);font-family:"Exo 2",sans-serif;font-size:72px;font-weight:700;line-height:1;padding-top:30px}
.quote-body h4{font-size:17px;font-weight:500}
.quote-body p{font-size:15px;color:var(--grey);line-height:28px;margin-top:12px}
.touch-photo{left:0;top:2065px;width:1200px;height:710px;background:linear-gradient(180deg,#5a6270 0%,#8c8d8a 35%,#b88a55 62%,#6e6149 85%,#4e4a3c 100%)}
.touch{left:609px;top:2135px;width:490px;color:var(--white)}
.touch h2{font-size:40px;font-weight:600}
.touch p{font-size:17px;line-height:30px;margin-top:14px}
.field{background:var(--white);border-radius:6px;font-size:15px;color:#444;padding:18px 19px}
.footer{left:0;top:2773px;width:1200px;height:357px;background:var(--black)}
.fnav{font-size:15.5px}
.info{display:flex;gap:14px;color:var(--white)}
.info h5{font-size:17px;font-weight:500}
.info p{font-size:15px;line-height:26px;margin-top:2px}
.rule{height:1px;background:#333}
</style>
</head>
<body>

<!-- Hero -->
<div class="abs hero" role="img" aria-label="Dump truck parked beside piles of dirt and sand at a work site"></div>
<svg class="abs" style="left:0;top:490px" width="1200" height="135">
  <path d="M0,12 Q100,12 160,20 L598,128 L1040,20 Q1100,12 1200,12 L1200,135 L0,135Z" fill="#fff"/>
  <path d="M150,18 L598,127 L1050,18" stroke="#e31b2d" stroke-width="5" fill="none"/>
</svg>

<!-- Header -->
<div class="abs" style="left:0;top:0;width:1200px;height:102px;background:#fff"></div>
<div class="abs brand" style="left:112px;top:34px"><span>SUMMIT AGGREGATES</span><span class="brand-square"></span></div>

<div class="abs contact-item" style="left:518px;top:17px">
  <div class="round-icon"><svg width="20" height="20" viewBox="0 0 24 24"><path d="M6.6 10.8a15 15 0 0 0 6.6 6.6l2.2-2.2a1 1 0 0 1 1-.25 11.4 11.4 0 0 0 3.6.57 1 1 0 0 1 1 1V20a1 1 0 0 1-1 1A17 17 0 0 1 3 4a1 1 0 0 1 1-1h3.5a1 1 0 0 1 1 1c0 1.25.2 2.45.57 3.57a1 1 0 0 1-.25 1z" fill="#fff"/></svg></div>
  <div>Get In Touch<br><b>+1 555-010-2240</b></div>
</div>
<div class="abs contact-item" style="left:736px;top:17px">
  <div class="round-icon"><svg width="22" height="22" viewBox="0 0 24 24"><circle cx="12" cy="12" r="9" fill="#fff"/><path d="M12 7v5l3 2" stroke="#e31b2d" stroke-width="2.2" fill="none" stroke-linecap="round"/></svg></div>
  <div>Business Hours<br><b>8:00 AM - 6:00 PM</b></div>
</div>
<div class="abs btn btn-blue" style="left:966px;top:16px;width:124px;height:42px">Get a Quote</div>

<svg class="abs" style="left:0;top:80px" width="1200" height="50">
  <polygon points="488,2 1200,2 1200,50 470,50" fill="#1a7bb5"/>
  <polygon points="484,0 1200,0 1200,4 483,4" fill="#e31b2d"/>
  <polygon points="484,0 488,0 470,50 466,50" fill="#e31b2d"/>
</svg>
<div class="abs nav" style="left:511px;top:99px">
  <span>HOME</span><span class="sep">|</span><span>OUR SERVICES</span><span class="sep">|</span><span>ABOUT US</span><span class="sep">|</span><span>TESTIMONIAL</span><span class="sep">|</span><span>CONTACT</span>
</div>

<!-- Services -->
<h2 class="abs heading section-title" style="top:672px">OUR SERVICES</h2>

<div class="abs card" style="left:85px;top:766px">
  <div class="service-icon" role="img" aria-label="Dirt service icon"></div>
  <h3>DIRT</h3>
  <p>Sed ut perspiciati unde omnis iste natus error sit voluptatem accusantium ue laudantium, totam rem.</p>
</div>
<div class="abs card" style="left:351px;top:766px">
  <div class="service-icon" role="img" aria-label="Landscape bark service icon"></div>
  <h3>LANDSCAPE BARK</h3>
  <p>Sed ut perspiciati unde omnis iste natus error sit voluptatem accusantium ue laudantium, totam rem.</p>
</div>
<svg class="abs" style="left:607px;top:776px" width="236" height="260"><path d="M8,0 Q2,0 2,10 V256 H224 Q232,256 234,246" stroke="#e31b2d" stroke-width="2" fill="none"/></svg>
<div class="abs card" style="left:618px;top:766px">
  <div class="service-icon" role="img" aria-label="Gravel service icon"></div>
  <h3>GRAVEL</h3>
  <p>Sed ut perspiciati unde omnis iste natus error sit voluptatem accusantium ue laudantium, totam rem.</p>
</div>
<div class="abs card" style="left:885px;top:766px">
  <div class="service-icon" role="img" aria-label="Landscape materials service icon"></div>
  <h3>LANDSCAPE MATERIALS</h3>
  <p>Sed ut perspiciati unde omnis iste natus error sit voluptatem accusantium ue laudantium, totam rem.</p>
</div>

<!-- About -->
<div class="abs about"></div>
<div class="abs" role="img" aria-label="Loader filling a dump truck beside a sand and gravel pile" style="left:694px;top:1096px;width:506px;height:430px;background:linear-gradient(180deg,#5d84b8 0%,#a9b9c8 25%,#cbb38e 55%,#9a9892 100%);clip-path:polygon(91px 0,100% 0,100% 100%,0 100%)"></div>
<svg class="abs" style="left:0;top:1096px" width="1200" height="430">
  <path d="M773,0 L695,370 L710,370" stroke="#fff" stroke-width="2" fill="none"/>
</svg>
<div class="abs about-text">
  <h2 class="heading">ABOUT US</h2>
  <p>Lorem ipsum dolor sit amet, consectetur adipiscing elit, sed do eiusmo tempor incididunt ut labore et dolore magna aliqua. Ut enim ad minimm, quis nostrud exercitation ullamco laboris nisi ut aliquip ex ea commodo conequat. Duis aute irure dolor in reprehenderit in voluptate velit esse cillum dolore eu fugiat nulla pariatur. Excepteur sint occaecat cupidatat non proident, sunt in culpa qui officia deserunt mollit anim id est laborum.</p>
</div>
<div class="abs btn btn-red" style="left:114px;top:1417px;width:124px;height:42px">Learn More</div>

<!-- Testimonials -->
<h2 class="abs heading section-title" style="top:1590px">TESTIMONIALS</h2>

<div class="abs quote-wrap" style="left:134px;top:1702px"><div class="quote-card" style="clip-path:polygon(0 0,100% 0,95.2% 100%,0 100%)"></div></div>
<div class="abs quote-badge" style="left:156px;top:1667px">”</div>
<div class="abs quote-body" style="left:158px;top:1768px;width:400px">
  <h4>Daniel Reyes</h4>
  <p>Ut enim ad minima veniam, quis nostr exercit lorem ip ationem ullam corporis suscipit laborim, nisit utipsumi aliquid ex ea commodi consequatur.</p>
</div>

<div class="abs quote-wrap" style="left:612px;top:1702px"><div class="quote-card" style="clip-path:polygon(4.8% 0,100% 0,100% 100%,0 100%)"></div></div>
<div class="abs quote-badge" style="left:653px;top:1667px">”</div>
<div class="abs quote-body" style="left:655px;top:1768px;width:400px">
  <h4>Daniel Reyes</h4>
  <p>Ut enim ad minima veniam, quis nostr exercit lorem ip ationem ullam corporis suscipit laborim, nisit utipsumi aliquid ex ea commodi consequatur.</p>
</div>

<div class="abs btn btn-blue" style="left:538px;top:1964px;width:124px;height:42px">View All</div>

<!-- Get in touch -->
<div class="abs touch-photo" role="img" aria-label="Semi truck with trailer driving on a dusty country road at sunset"></div>
<div class="abs touch">
  <h2 class="heading">GET IN TOUCH</h2>
  <p>Sed ut perspiciatis unde omnis iste natus errosit voluptatem accusantium doloremque laudantium, totam rem aperiam.</p>
</div>
<div class="abs field" style="left:610px;top:2294px;width:229px;height:55px">First Name</div>
<div class="abs field" style="left:857px;top:2294px;width:229px;height:55px">Last Name</div>
<div class="abs field" style="left:610px;top:2362px;width:478px;height:54px">Email ID</div>
<div class="abs field" style="left:610px;top:2430px;width:478px;height:124px">Message</div>
<div class="abs btn btn-red" style="left:610px;top:2577px;width:124px;height:43px">Submit</div>

<!-- Footer -->
<div class="abs footer"></div>
<svg class="abs" style="left:0;top:2650px" width="1200" height="125">
  <path d="M0,123 Q80,123 120,118 L598,6 L1080,118 Q1120,123 1200,123 L1200,125 L0,125Z" fill="#050505"/>
  <path d="M110,122 L598,4 L1090,122" stroke="#1a7bb5" stroke-width="6" fill="none"/>
</svg>
<div class="abs brand" style="left:0;width:1200px;top:2772px;justify-content:center"><span>SUMMIT AGGREGATES</span><span class="brand-square"></span></div>

<div class="abs nav fnav" style="left:307px;top:2858px">
  <span>HOME</span><span class="sep">|</span><span>OUR SERVICES</span><span class="sep">|</span><span>ABOUT US</span><span class="sep">|</span><span>TESTIMONIALS</span><span class="sep">|</span><span>CONTACT</span>
</div>
<div class="abs rule" style="left:111px;top:2917px;width:978px"></div>

<div class="abs info" style="left:111px;top:2950px">
  <svg width="22" height="26" viewBox="0 0 24 28" fill="none" stroke="#fff" stroke-width="1.8"><path d="M12 26 C4 16 3 13 3 10 a9 9 0 0 1 18 0 c0 3 -1 6 -9 16z"/><circle cx="12" cy="10" r="3"/></svg>
  <div><h5>ADDRESS</h5><p>Summit Aggregates,<br>Address comes here</p></div>
</div>
<div class="abs info" style="left:367px;top:2950px">
  <svg width="24" height="22" viewBox="0 0 26 22" fill="none" stroke="#fff" stroke-width="1.8"><rect x="1" y="2" width="24" height="18" rx="1"/><path d="M1 3 l12 9 12-9"/></svg>
  <div><h5>EMAIL</h5><p>info@summitaggregates.com</p></div>
</div>
<div class="abs info" style="left:661px;top:2950px">
  <svg width="24" height="24" viewBox="0 0 24 24" fill="none" stroke="#fff" stroke-width="1.6"><path d="M6.6 10.8a15 15 0 0 0 6.6 6.6l2.2-2.2a1 1 0 0 1 1-.25 11.4 11.4 0 0 0 3.6.57 1 1 0 0 1 1 1V20a1 1 0 0 1-1 1A17 17 0 0 1 3 4a1 1 0 0 1 1-1h3.5a1 1 0 0 1 1 1c0 1.25.2 2.45.57 3.57a1 1 0 0 1-.25 1z"/></svg>
  <div><h5>PHONE</h5><p>+1 555-010-2240</p></div>
</div>
<div class="abs info" style="left:906px;top:2950px">
  <svg width="22" height="22" viewBox="0 0 24 24"><circle cx="12" cy="12" r="10" fill="#fff"/><path d="M12 6v6l-3 2" stroke="#050505" stroke-width="2.2" fill="none" stroke-linecap="round"/></svg>
  <div><h5>HOURS</h5><p>Mon - Fri&nbsp; 8am - 6pm</p></div>
</div>

<div class="abs rule" style="left:111px;top:3063px;width:978px"></div>
<div class="abs" style="left:0;width:1200px;top:3087px;text-align:center;color:#fff;font-size:15px">2023 Summit Aggregates. All Rights Reserved.</div>

</body>
</html>
```